Brightway Haul & Upkeep Services, are a company that offers a 'one stop shop' pre-move clean up a

I have already selected a logo which I would like on the front of the business cards along with phone numbers, web address and email which are:
0487650392
www.brightwayhaul.com.au
brightwayhaulandupkeep@mailbox.example

On the back of the card I would like to list some of the types of service we offer (clean - move - repairs/maintenance) which are:
CLEAN - windows, gutters, solar panels, driveways/paths, carpets.
MOVE - Small/medium size house/office moves, large item pick-up & delivery, yard clean-up and removal.
General maintenance and repairs.

I would like the blue logo on a gray background.

Thanks

```html
<!DOCTYPE html>
<html lang="en">
<head>
<meta charset="utf-8">
<title>Brightway Haul &amp; Upkeep Services – Business Card</title>
<link href="https://fonts.googleapis.com/css2?family=Arimo:wght@400;700&display=swap" rel="stylesheet">
<style>
  :root {
    --brand-blue: #3170b7;
    --panel-grey: #e6e7e8;
    --divider-white: #ffffff;
    --text-dark: #555659;
    --footer-text: #e4e8f0;
    --footer-label: #d3dbe8;
  }
  * { margin: 0; padding: 0; box-sizing: border-box; }
  html, body {
    width: 1009px;
    height: 1200px;
    overflow: hidden;
    background: var(--divider-white);
    font-family: "Arimo", Arial, sans-serif;
  }
  .card {
    position: relative;
    width: 1009px;
    height: 1200px;
    background: var(--divider-white);
  }
  .top-band {
    position: absolute; left: 0; top: 0;
    width: 100%; height: 278px;
    background: var(--brand-blue);
  }
  .brand-panel {
    position: absolute; left: 0; top: 278px;
    width: 100%; height: 318px;
    background: var(--panel-grey);
  }
  .services-panel {
    position: absolute; left: 0; top: 604px;
    width: 100%; height: 396px;
    background: var(--panel-grey);
  }
  .contact-band {
    position: absolute; left: 0; top: 1000px;
    width: 100%; height: 200px;
    background: var(--brand-blue);
  }
  .centered { position: absolute; left: 0; width: 100%; text-align: center; }

  .brand-name {
    color: var(--brand-blue);
    font-weight: 700;
    text-transform: uppercase;
  }
  .brand-name .line-main { display: block; font-size: 74px; line-height: 84px; letter-spacing: 1px; }
  .brand-name .line-sub { display: block; font-size: 38px; line-height: 46px; letter-spacing: 0.5px; }

  .service-tags {
    top: 476px;
    font-size: 23px; font-weight: 700;
    color: var(--text-dark);
    line-height: 28px;
  }
  .service-tags .sep {
    display: inline-block; width: 4px; height: 13px;
    background: var(--text-dark);
    margin: 0 38px; vertical-align: middle;
  }
  .abn {
    top: 548px;
    font-size: 33px; font-weight: 700;
    color: var(--text-dark);
    line-height: 38px;
  }

  .service-column {
    position: absolute; top: 700px;
    text-align: center;
    color: var(--brand-blue);
  }
  .service-column.clean { left: 52px; width: 400px; }
  .service-column.move { left: 558px; width: 400px; }
  .service-column h2 {
    font-size: 31px; font-weight: 700;
    line-height: 44px; margin-bottom: 0;
  }
  .service-column ul { list-style: none; }
  .service-column li { font-size: 26px; line-height: 41.5px; }
  .service-column .pipe {
    display: inline-block; width: 2px; height: 20px;
    background: var(--brand-blue);
    margin: 0 4px; vertical-align: -2px;
  }
  .column-divider {
    position: absolute; left: 504px; top: 706px;
    width: 3px; height: 194px;
    background: var(--brand-blue);
  }
  .general-note {
    top: 940px;
    font-size: 26px; font-weight: 700;
    color: var(--brand-blue);
    line-height: 32px;
  }

  .contact-list {
    top: 1016px;
    font-size: 33px;
    color: var(--footer-text);
    line-height: 42.5px;
  }
  .contact-list .label { font-weight: 700; color: var(--footer-label); }
</style>
</head>
<body>
<main class="card">
  <div class="top-band"></div>
  <section class="brand-panel"></section>
  <section class="services-panel"></section>
  <footer class="contact-band"></footer>

  <h1 class="centered brand-name" style="top:302px;">
    <span class="line-main">Brightway Haul</span>
    <span class="line-sub">&amp; Upkeep Services</span>
  </h1>

  <p class="centered service-tags">CLEAN<span class="sep"></span>MOVE<span class="sep"></span>REPAIRS/MAINTENANCE</p>
  <p class="centered abn">ABN 58190447326</p>

  <div class="service-column clean">
    <h2>CLEAN</h2>
    <ul>
      <li>Windows<span class="pipe"></span>Gutters</li>
      <li>Solar panels</li>
      <li>Driveways/Paths</li>
      <li>Carpets.</li>
    </ul>
  </div>
  <div class="column-divider"></div>
  <div class="service-column move">
    <h2>MOVE</h2>
    <ul>
      <li>Small/Medium size House</li>
      <li>Office moves</li>
      <li>Large item pick-up &amp; delivery</li>
      <li>Yard clean-up and removal.</li>
    </ul>
  </div>
  <p class="centered general-note">GENERAL MAINTENANCE AND REPAIRS.</p>

  <div class="centered contact-list">
    <p><span class="label">Call:</span> Dean or Marco</p>
    <p><span class="label">Phone:</span> 0487650392</p>
    <p><span class="label">Website:</span> www.brightwayhaul.com.au</p>
    <p><span class="label">E-mail:</span> brightwayhaulandupkeep@mailbox.example</p>
  </div>
</main>
</body>
</html>
```